Vornel Wellness Business Card

A Double Sided Business Card

I am a private company in Melbourne, Australia, working in the Health industry. I am a nutritionist and lifestyle coach, whom specialises in using raw foods ie. fruits/nuts/vegetables to help heal my clients and enable them to achieve their ultimate state of health.

I want a sophisticated design and colour for my card that appeals to both men and women from teenage through to elderly.

Front of Card:

Red apple peel spiral in the shape of an apple. I would like a leaf/leaves coming off the stem of the apple. Please see attachments for example.

***On Right Hand side of Image is business Name: Vornel Wellness

Underneath LOGO use slogan " Let Food Be Your Medicine"

***Use Deep Red and Blues for Text Colouring

Back of Card:

Marisol Dekkert
Nutritional Specialist and Lifestyle Coach

Specialising in: Diseased Conditions
Weight Management
Achieving your Ultimate State of Health

enquiries@vornelwellness.com.au 0457 396 504

**Make sure the front design of the card flows onto the back.
Updates

Email address has been amended, Also more specific details have been given for apple peel Image, and another image attached as example of Leaf on stem of apple.

I little more insight into what sort of feel were trying to create. We're apart of the health industry, and we want the card to have a medical/clinical feeling about it.

Target Market(s)

Males and Females from teenages to elderly

Industry/Entity Type

Business

Requirements
Must have
• Red Apple Peel Spiral, in the shape of an apple, with a leaf/leaves attached to stem.
***Must be in the shape of an apple
***Please use coloring on inside of apple peel to resemble inside of an apple.
Nice to have
• I would like my card to have a clinical feel.
Should not have
• We don't want the image of the apple to look like a Christmas decoration

```html
<!DOCTYPE html>
<html lang="en">
<head>
<meta charset="utf-8">
<title>Marisol Dekkert – Vornel Wellness Business Card</title>
<link rel="stylesheet" href="https://fonts.googleapis.com/css2?family=Questrial&display=swap">
<style>
  :root {
    --navy: #1b1e4b;
    --navy-deep: #12143a;
    --red: #d8232a;
    --red-dark: #9e1016;
    --paper: #f4f4f6;
    --silver: #c9cad0;
    --ink-light: #e6e7ee;
    --ink-grey: #3a3a44;
    --accent-blue: #2a2f7a;
    --accent-blue-light: #4a52b8;
  }
  * { margin: 0; padding: 0; box-sizing: border-box; }
  html, body {
    width: 1200px; height: 741px; overflow: hidden;
    background: #ffffff;
  }
  .card {
    position: relative;
    width: 1200px; height: 741px;
    overflow: hidden;
    font-family: "Questrial", "Century Gothic", sans-serif;
    background: var(--navy);
  }
  .card-background { position: absolute; inset: 0; width: 1200px; height: 741px; }

  .name {
    position: absolute; left: 122px; top: 110px;
    font-size: 55px; font-weight: 400; line-height: 1;
    color: var(--red); letter-spacing: 0.5px;
  }
  .role {
    position: absolute; left: 126px; top: 173px;
    font-size: 37px; line-height: 40px;
    color: var(--ink-light);
  }
  .divider {
    position: absolute; left: 605px; top: 97px;
    width: 3px; height: 170px; background: var(--ink-light);
  }
  .contact {
    position: absolute; left: 632px; display: flex; align-items: center;
    font-size: 30px; color: #ffffff; line-height: 1; white-space: nowrap;
  }
  .contact-email { top: 132px; }
  .contact-phone { top: 200px; }
  .contact-icon { width: 38px; height: 38px; margin-right: 18px; flex: none; }

  .specialties-heading {
    position: absolute; left: 115px; top: 418px;
    font-size: 40px; font-weight: 400; color: var(--accent-blue);
  }
  .specialties-heading .soft { color: var(--accent-blue-light); }
  .specialties {
    position: absolute; left: 118px; top: 487px;
    list-style: none; font-size: 34px; line-height: 50px;
    color: var(--ink-grey);
  }
  .specialties li::before { content: "·"; margin-right: 12px; }

  .apple-artwork {
    position: absolute; left: 1000px; top: 522px;
    width: 150px; height: 160px;
    border-radius: 48% 48% 46% 46% / 52% 52% 48% 48%;
    background: radial-gradient(circle at 40% 35%, #f04b4f 0%, #c8141c 55%, #7e0a10 100%);
  }
</style>
</head>
<body>
<div class="card">
  <svg class="card-background" viewBox="0 0 1200 741" aria-hidden="true">
    <defs>
      <linearGradient id="bar-red" x1="0" y1="0" x2="1" y2="0">
        <stop offset="0" stop-color="#9e1016"/>
        <stop offset="0.5" stop-color="#e0262d"/>
        <stop offset="1" stop-color="#9e1016"/>
      </linearGradient>
      <linearGradient id="sweep-silver" x1="0" y1="0" x2="1" y2="1">
        <stop offset="0" stop-color="#b9bac2"/>
        <stop offset="0.5" stop-color="#e9e9ee"/>
        <stop offset="1" stop-color="#cfd0d6"/>
      </linearGradient>
      <radialGradient id="navy-glow" cx="0.55" cy="0.2" r="0.7">
        <stop offset="0" stop-color="#262a62"/>
        <stop offset="1" stop-color="#15173e"/>
      </radialGradient>
    </defs>
    <rect width="1200" height="741" fill="url(#navy-glow)"/>
    <path d="M0 285 C 300 300, 700 350, 1200 470 L 1200 741 L 0 741 Z" fill="url(#sweep-silver)"/>
    <path d="M0 330 C 320 360, 760 420, 1200 520 L 1200 741 L 0 741 Z" fill="#f6f6f8"/>
    <path d="M0 695 C 220 698, 420 715, 560 741 L 0 741 Z" fill="var(--navy-deep)"/>
    <path d="M0 672 C 240 676, 460 700, 610 741 L 560 741 C 420 715, 220 698, 0 695 Z" fill="#c5c6cd"/>
    <rect x="15" y="0" width="18" height="280" fill="url(#bar-red)"/>
    <rect x="40" y="0" width="28" height="280" fill="url(#bar-red)"/>
    <rect x="75" y="0" width="18" height="280" fill="url(#bar-red)"/>
  </svg>

  <h1 class="name">Marisol Dekkert</h1>
  <p class="role">Nutritional Specialist<br>Lifestyle Coach</p>
  <div class="divider"></div>

  <p class="contact contact-email">
    <svg class="contact-icon" viewBox="0 0 44 44" aria-hidden="true" fill="none" stroke="#d8232a" stroke-width="2.5">
      <circle cx="22" cy="22" r="18"/>
      <ellipse cx="22" cy="22" rx="8" ry="18"/>
      <line x1="4" y1="22" x2="40" y2="22"/>
      <path d="M7 13 H37 M7 31 H37"/>
    </svg>
    enquiries@vornelwellness.com.au
  </p>
  <p class="contact contact-phone">
    <svg class="contact-icon" viewBox="0 0 44 44" aria-hidden="true">
      <path d="M12 4 L18 14 L14 18 C16 24 20 28 26 30 L30 26 L40 32 L36 40 C20 40 4 24 4 8 Z" fill="#d8232a"/>
    </svg>
    0457 396 504
  </p>

  <h2 class="specialties-heading">Speci<span class="soft">alising in:</span></h2>
  <ul class="specialties">
    <li>Diseased Conditions</li>
    <li>Weight Management</li>
    <li>Achieving your Ultimate State of Health</li>
  </ul>

  <div class="apple-artwork" role="img" aria-label="Red apple peel spiral shaped like an apple"></div>
</div>
</body>
</html>
```